Melorix artwork for new single release

I need Melorix artwork creating to release a new single on there.

The specs are:

Ideal size: 3000 x 3000 pixels
Minimum size: 1400 x 1400 pixels
Aspect ratio: 1:1 (must be a perfect square)
File format: JPG or PNG
Color space: sRGB
File size: Max 4MB

The song is called "Was It Ever Rain?"
The artist is "Martin Hollow"

We have no images of Martin, so it really is open to imagination.

Target Market(s)

Melorix listeners

Industry/Entity Type

Music

```html
<!DOCTYPE html>
<html lang="en">
<head>
<meta charset="utf-8">
<title>Was It Ever Rain? — Martin Hollow</title>
<link rel="stylesheet" href="https://fonts.googleapis.com/css2?family=IM+Fell+English:ital@0;1&family=Montserrat:wght@500&display=swap">
<style>
  :root {
    --night: #15143e;
    --indigo: #26246a;
    --violet: #5b449f;
    --plum: #7a3f9a;
    --magenta: #c04c8e;
    --rose: #e6a7c8;
    --lilac: #a79ae0;
    --periwinkle: #6f66c8;
    --glow: #5a62e0;
    --ink: #ffffff;
  }
  html, body {
    margin: 0;
    padding: 0;
    width: 1200px;
    height: 1200px;
    overflow: hidden;
    background: var(--night);
  }
  .cover {
    position: relative;
    width: 1200px;
    height: 1200px;
    overflow: hidden;
    background: var(--indigo);
  }
  .cover__artwork {
    position: absolute;
    inset: 0;
  }
  .cover__backdrop {
    position: absolute;
    inset: 0;
    background:
      radial-gradient(ellipse 90px 120px at 50% 52%, rgba(90,98,224,0.9) 0%, rgba(90,98,224,0) 100%),
      linear-gradient(180deg, #2a2a78 0%, #22206a 55%, var(--night) 100%);
  }
  .cover__figure {
    position: absolute;
    top: -40px;
    bottom: -40px;
    width: 640px;
    filter: blur(6px);
  }
  .cover__figure--left {
    left: -60px;
    border-radius: 30% 62% 40% 20% / 30% 48% 52% 40%;
    background:
      radial-gradient(ellipse 260px 200px at 60% 22%, rgba(230,167,200,0.85) 0%, rgba(230,167,200,0) 100%),
      radial-gradient(ellipse 300px 260px at 40% 40%, var(--magenta) 0%, rgba(192,76,142,0) 100%),
      radial-gradient(ellipse 240px 200px at 70% 60%, rgba(230,167,200,0.6) 0%, rgba(230,167,200,0) 100%),
      linear-gradient(180deg, var(--plum) 0%, var(--violet) 55%, #2c2670 100%);
  }
  .cover__figure--right {
    right: -60px;
    border-radius: 62% 30% 20% 40% / 48% 30% 40% 52%;
    background:
      radial-gradient(ellipse 260px 220px at 45% 28%, rgba(200,190,240,0.85) 0%, rgba(200,190,240,0) 100%),
      radial-gradient(ellipse 280px 260px at 55% 50%, var(--lilac) 0%, rgba(167,154,224,0) 100%),
      linear-gradient(180deg, var(--periwinkle) 0%, var(--violet) 60%, #2c2670 100%);
  }
  .cover__gap {
    position: absolute;
    left: 330px;
    top: 700px;
    width: 540px;
    height: 560px;
    border-radius: 45% 45% 0 0 / 30% 30% 0 0;
    background: linear-gradient(180deg, #1e1d5c 0%, #131236 100%);
    filter: blur(14px);
  }
  .cover__neck-gap {
    position: absolute;
    left: 555px;
    top: -20px;
    width: 90px;
    height: 760px;
    background: linear-gradient(180deg, #27276e 0%, #2b2d86 60%, #1e1d5c 100%);
    filter: blur(16px);
  }
  .cover__title {
    position: absolute;
    left: 0;
    right: 0;
    top: 0;
    margin: 0;
    font-weight: 400;
    color: var(--ink);
  }
  .cover__title-lead {
    position: absolute;
    left: 0;
    right: 0;
    top: 760px;
    font-family: "IM Fell English", Georgia, serif;
    font-style: italic;
    font-size: 60px;
    line-height: 1;
    text-align: center;
  }
  .cover__title-main {
    position: absolute;
    left: 0;
    right: 0;
    top: 830px;
    font-family: "IM Fell English", Georgia, serif;
    font-size: 88px;
    line-height: 1;
    text-align: center;
    text-transform: uppercase;
  }
  .cover__artist {
    position: absolute;
    left: 0;
    right: 0;
    top: 936px;
    margin: 0;
    font-family: "Montserrat", Arial, sans-serif;
    font-size: 40px;
    font-weight: 500;
    letter-spacing: 2px;
    line-height: 1;
    text-align: center;
    color: var(--ink);
  }
</style>
</head>
<body>
  <main class="cover">
    <div class="cover__artwork" role="img" aria-label="Illustration: two faceted, prismatic figures in pink, violet and blue facing each other in profile against a deep indigo night, with a small glowing crystal heart between them">
      <div class="cover__backdrop"></div>
      <div class="cover__figure cover__figure--left"></div>
      <div class="cover__figure cover__figure--right"></div>
      <div class="cover__neck-gap"></div>
      <div class="cover__gap"></div>
    </div>
    <h1 class="cover__title">
      <span class="cover__title-lead">Was It</span>
      <span class="cover__title-main">Ever Rain?</span>
    </h1>
    <p class="cover__artist">Martin Hollow</p>
  </main>
</body>
</html>
```